Summit Bodyform Gym Website

We need a website design for our gym.

Summit is the UAE's first calisthenics and parkour gym. The theme under which the gym revolves is that one does not require any machinery to workout as our bodies could be themselves the machinery. The gym is designed to be the more of a social hub rather than an "in-and-out" gym, where people come train, have fun, hang out and socialize for a few hours rather than just train for 60 minutes then leave. The gym is designed to be a big open space with lots of natural sunlight, natural wood and plants all over the place to create a natural and refreshing setting. We also use recycled material throughout the gym and recycle our waste as being green is part of our philosophy. We currently also have some of the world's top and most recognized calisthenics athletes working with us.

We would like our website to reflect all that as well as provide a simple, interactive and fun way for visitors to be able to get class and gym information, check out gym media and contact us for bookings.

Target Market(s)

Ages 15-35

Industry/Entity Type

Fitness

Coding

Coded - Design and coding required

Number of Pages Required

4 page

Font styles to use
Decorative

Colors
0792cd

Requirements
Must have
• Class descriptions
• Gym description
• Class schedules
• Trainer profiles
• Gym philosophy
• Contact Details
Nice to have
• A link to contact us directly for a free first trial class

```html
<!DOCTYPE html>
<html lang="en">
<head>
<meta charset="utf-8">
<title>Summit Gym</title>
<link rel="stylesheet" href="https://fonts.googleapis.com/css2?family=Anton&family=Arimo:wght@400;700&family=Exo+2:wght@400;500&family=Roboto+Condensed:wght@400;700&display=swap">
<style>
:root{
  --brand:#0792cd;
  --band:#0b9ec4;
  --dark:#1f1f1f;
  --footer:#232323;
  --ink:#1a1a1a;
  --body:#333333;
  --soft:#e9e9e9;
  --white:#ffffff;
}
*{box-sizing:border-box;margin:0;padding:0}
html,body{width:1200px;height:2844px;overflow:hidden}
body{background:var(--white);font-family:"Arimo",Arial,sans-serif;color:var(--body);position:relative}

.topbar{position:absolute;top:0;left:0;width:1200px;height:38px;background:var(--dark);color:#e6e6e6;font-size:13px}
.topbar .contact-item{position:absolute;top:11px;display:flex;align-items:center;gap:8px}
.topbar .social{position:absolute;right:70px;top:14px;display:flex;gap:12px}
.topbar .social span{width:9px;height:9px;border-radius:50%;background:#bdbdbd;display:block}

.header{position:absolute;top:38px;left:0;width:1200px;height:123px;background:var(--white)}
.wordmark{font-family:"Exo 2",sans-serif;font-weight:500;white-space:nowrap}
.header .wordmark{position:absolute;left:64px;top:36px;font-size:40px;color:var(--ink)}
.nav{position:absolute;top:57px;left:0;width:1200px;font-size:13px;font-weight:700;color:var(--ink);letter-spacing:.3px}
.nav a{position:absolute;color:inherit;text-decoration:none;white-space:nowrap}
.nav a.drop::after{content:"";display:inline-block;margin-left:6px;vertical-align:middle;border-left:4px solid transparent;border-right:4px solid transparent;border-top:4px solid var(--brand)}

.hero{position:absolute;top:161px;left:0;width:1200px;height:603px;background:linear-gradient(180deg,#a4693f 0%,#b27a4b 40%,#6e4a30 62%,#3a3a3a 80%,#2c2c2c 100%)}
.hero-caption{position:absolute;left:61px;top:157px;width:680px;height:193px;background:rgba(7,146,205,.82);color:var(--white);padding:30px 0 0 28px}
.hero-caption .line1{font-family:"Roboto Condensed",sans-serif;font-weight:700;font-size:50px;line-height:1.1}
.hero-caption .line2{font-size:44px;line-height:1.35}

.welcome{position:absolute;top:764px;left:0;width:1200px;height:544px;text-align:center}
.welcome h1{position:absolute;top:82px;left:0;width:1200px;font-family:"Anton",sans-serif;font-weight:400;font-size:50px;color:#000;font-variant:small-caps;letter-spacing:.5px}
.rule{display:block;height:4px;background:var(--brand)}
.welcome .rule{position:absolute;top:157px;left:484px;width:180px}
.welcome .copy{position:absolute;top:193px;left:70px;width:1060px;font-size:14px;line-height:22.5px;color:var(--body)}
.welcome .copy p+p{margin-top:21px}
.btn-outline{display:inline-flex;align-items:center;justify-content:center;border:2px solid var(--ink);background:var(--white);color:var(--ink);text-decoration:none}
.welcome .btn-outline{position:absolute;top:402px;left:468px;width:198px;height:50px;font-size:16px;letter-spacing:.5px}

.services{position:absolute;top:1308px;left:0;width:1200px;height:351px;background:var(--band);color:var(--white)}
.services h2{position:absolute;top:38px;left:0;width:1200px;text-align:center;font-family:"Exo 2",sans-serif;font-weight:500;font-size:40px;letter-spacing:.5px}
.services .rule{position:absolute;top:97px;left:537px;width:130px;background:var(--ink)}
.service-list{position:absolute;top:139px;left:60px;display:flex;gap:32px}
.service{width:190px;height:157px;border:1.5px solid rgba(255,255,255,.55);border-radius:14px;display:flex;flex-direction:column;align-items:center;padding-top:20px}
.service .icon{width:83px;height:83px;border-radius:50%;background:var(--white);display:flex;align-items:center;justify-content:center}
.service .label{margin-top:12px;font-family:"Exo 2",sans-serif;font-size:21px}

.gym{position:absolute;top:1659px;left:0;width:1200px;height:867px;background:var(--soft);overflow:hidden}
.section-title{position:absolute;top:123px;left:61px;height:62px;border-left:6px solid var(--ink);padding-left:18px;font-family:"Exo 2",sans-serif;font-weight:400;font-size:40px;line-height:62px;color:var(--ink)}
.section-title .accent{color:var(--brand)}
.card-list{position:absolute;top:256px;left:59px;display:flex;gap:46px}
.card{width:330px;height:531px;background:var(--white);text-align:center}
.card .photo{height:222px}
.card h3{margin-top:26px;font-family:"Exo 2",sans-serif;font-weight:400;font-size:30px;color:var(--ink)}
.card .rule{width:80px;margin:12px auto 0}
.card p{margin:12px auto 0;width:286px;font-family:"Exo 2",sans-serif;font-size:15px;line-height:22px;color:#444}
.card .btn-outline{margin-top:32px;width:140px;height:42px;font-family:"Exo 2",sans-serif;font-size:15px}

.footer{position:absolute;top:2526px;left:0;width:1200px;height:318px;background:var(--footer);color:#bdbdbd;text-align:center;font-family:"Exo 2",sans-serif}
.footer .wordmark{position:absolute;left:0;top:56px;width:1200px;color:var(--white);font-size:36px}
.footer .address{position:absolute;top:152px;left:0;width:1200px;font-size:17px;line-height:27px}
.footer .divider{position:absolute;top:227px;left:325px;width:550px;height:1px;background:#3a3a3a}
.footer .copyright{position:absolute;top:246px;left:0;width:1200px;font-size:15px}
</style>
</head>
<body>

<div class="topbar">
  <div class="contact-item" style="left:596px">
    <svg width="14" height="14" viewBox="0 0 24 24"><path fill="#e6e6e6" d="M6.6 10.8a15.1 15.1 0 0 0 6.6 6.6l2.2-2.2a1 1 0 0 1 1-.25 11.4 11.4 0 0 0 3.6.57 1 1 0 0 1 1 1V20a1 1 0 0 1-1 1A17 17 0 0 1 3 4a1 1 0 0 1 1-1h3.5a1 1 0 0 1 1 1c0 1.25.2 2.45.57 3.57a1 1 0 0 1-.25 1z"/></svg>
    <span>1300 552 408</span>
  </div>
  <div class="contact-item" style="left:757px">
    <svg width="16" height="12" viewBox="0 0 16 12"><rect x=".5" y=".5" width="15" height="11" fill="none" stroke="#e6e6e6"/><path d="M.5.5 8 7l7.5-6.5" fill="none" stroke="#e6e6e6"/></svg>
    <span>hello@summit-gym.com</span>
  </div>
  <div class="social" aria-hidden="true"><span></span><span></span><span></span><span></span><span></span><span></span></div>
</div>

<header class="header">
  <div class="wordmark">Summit</div>
  <nav class="nav">
    <a class="drop" style="left:317px">HOME</a>
    <a style="left:405px">ABOUT US</a>
    <a class="drop" style="left:521px">CLASSES</a>
    <a class="drop" style="left:624px">TRAINERS</a>
    <a style="left:739px">EVENT</a>
    <a style="left:827px">ELEMENTS</a>
    <a class="drop" style="left:944px">SHOP</a>
    <a style="left:1029px">CONTACT</a>
  </nav>
</header>

<section class="hero" role="img" aria-label="Gym interior with wooden wall of plant lettering above a rack of dumbbells and exercise balls">
  <div class="hero-caption">
    <div class="line1">Summit is the UAE's first</div>
    <div class="line2">calisthenics &amp; parkour gym</div>
  </div>
</section>

<section class="welcome">
  <h1>Welcome to Summit</h1>
  <span class="rule"></span>
  <div class="copy">
    <p>simply dummy text of the printing and typesetting industry. Lorem Ipsum has been the industry's standard dummy text ever since the 1500s, when an unknown printer took a galley of type and scrambled it to make a type specimen book. It has survived not only five centuries, but also the leap into electronic typesetting, remaining essentially unchanged. It was popularised in the 1960s with the release of transfer sheets containing Lorem Ipsum passages, and more recently with desktop publishing software like common layout programs including versions of Lorem Ipsum.</p>
    <p>Lorem Ipsum has been the industry's standard dummy text ever since the 1500s, when an unknown printer took a galley of type and scrambled it to make a type specimen book. It has survived not only five centuries, but also the leap into electronic typesetting, remaining essentially unchanged. It was popularised in the 1960s with the release of transfer sheets containing.</p>
  </div>
  <a class="btn-outline">READ MORE</a>
</section>

<section class="services">
  <h2>OUR SERVICES</h2>
  <span class="rule"></span>
  <div class="service-list">
    <div class="service">
      <div class="icon"><svg width="50" height="44" viewBox="0 0 50 44"><rect x="3" y="3" width="30" height="22" fill="none" stroke="#111" stroke-width="3"/><circle cx="38" cy="24" r="5" fill="#111"/><path d="M30 42v-8a8 8 0 0 1 16 0v8z" fill="#111"/><path d="M26 25l8 8" stroke="#111" stroke-width="3"/></svg></div>
      <div class="label">Class Description</div>
    </div>
    <div class="service">
      <div class="icon"><svg width="52" height="44" viewBox="0 0 52 44"><rect x="2" y="6" width="8" height="18" fill="#111"/><rect x="42" y="6" width="8" height="18" fill="#111"/><rect x="10" y="13" width="32" height="4" fill="#111"/><circle cx="26" cy="24" r="5" fill="#111"/><path d="M16 44v-8a10 8 0 0 1 20 0v8z" fill="#111"/></svg></div>
      <div class="label">Gym Description</div>
    </div>
    <div class="service">
      <div class="icon"><svg width="46" height="46" viewBox="0 0 46 46"><rect x="3" y="7" width="36" height="32" fill="none" stroke="#111" stroke-width="3"/><rect x="3" y="7" width="36" height="8" fill="#111"/><g fill="#111"><rect x="9" y="19" width="5" height="4"/><rect x="18" y="19" width="5" height="4"/><rect x="27" y="19" width="5" height="4"/><rect x="9" y="27" width="5" height="4"/><rect x="18" y="27" width="5" height="4"/></g><circle cx="35" cy="35" r="9" fill="#fff" stroke="#111" stroke-width="3"/><path d="M35 30v5h4" fill="none" stroke="#111" stroke-width="2"/></svg></div>
      <div class="label">Class Schedules</div>
    </div>
    <div class="service">
      <div class="icon"><svg width="50" height="42" viewBox="0 0 50 42"><path d="M8 4h6l4 26" fill="none" stroke="#111" stroke-width="4"/><path d="M4 32h42l2 6H6z" fill="#111"/><circle cx="28" cy="10" r="4" fill="#111"/><path d="M26 16l-4 14M28 16l8 10" stroke="#111" stroke-width="3"/></svg></div>
      <div class="label">Trainer Profiles</div>
    </div>
    <div class="service">
      <div class="icon"><svg width="50" height="46" viewBox="0 0 50 46"><circle cx="14" cy="32" r="10" fill="none" stroke="#111" stroke-width="3"/><path d="M14 32l10-18h14M24 14l-4-8h-6M36 14l4 22h6" fill="none" stroke="#111" stroke-width="3"/><path d="M32 6h10" stroke="#111" stroke-width="3"/></svg></div>
      <div class="label">Gym Philosophy</div>
    </div>
  </div>
</section>

<section class="gym">
  <h2 class="section-title">Gym <span class="accent">Description</span></h2>
  <div class="card-list">
    <article class="card">
      <div class="photo" role="img" aria-label="Calisthenics rig with gymnastic ring hanging from a steel frame" style="background:linear-gradient(160deg,#cfe0ea 0%,#5d7d96 45%,#2a2f35 100%)"></div>
      <h3>Calisthenics Gym</h3>
      <span class="rule"></span>
      <p>Curabitur fermentum odio ac enim interdum consequat. Sed vel faucibus leo. Ut turpis ipsum, fringilla eget vel faucibus leo. Ut turpis ipsum, fringilla tortor in, placerat rhoncus nibh. ..</p>
      <a class="btn-outline">Read More</a>
    </article>
    <article class="card">
      <div class="photo" role="img" aria-label="Open training floor with a black climbing and pull-up frame" style="background:linear-gradient(180deg,#e4e6e8 0%,#9a9ea3 50%,#4a4e52 100%)"></div>
      <h3>Calisthenics Gym</h3>
      <span class="rule"></span>
      <p>Curabitur fermentum odio ac enim interdum consequat. Sed vel faucibus leo. Ut turpis ipsum, fringilla eget vel faucibus leo. Ut turpis ipsum, fringilla tortor in, placerat rhoncus nibh. ..</p>
      <a class="btn-outline">Read More</a>
    </article>
    <article class="card">
      <div class="photo" role="img" aria-label="Athlete training on a blue steel bar structure inside the gym" style="background:linear-gradient(160deg,#2c3a55 0%,#3f6aa8 45%,#1d2230 100%)"></div>
      <h3>Calisthenics Gym</h3>
      <span class="rule"></span>
      <p>Curabitur fermentum odio ac enim interdum consequat. Sed vel faucibus leo. Ut turpis ipsum, fringilla eget vel faucibus leo. Ut turpis ipsum, fringilla tortor in, placerat rhoncus nibh. ..</p>
      <a class="btn-outline">Read More</a>
    </article>
  </div>
</section>

<footer class="footer">
  <div class="wordmark">Summit</div>
  <div class="address">45 Cedar Plaza, East 14th Street, Suite 310, UAE<br>844 555 0147 210 – hello@summit-gym.com</div>
  <div class="divider"></div>
  <div class="copyright">Copyright © 2015 – Summit Gym – All rights reserved.</div>
</footer>

</body>
</html>
```